Business card for a Exhibition booth fabrication company

Hi. My company would like to change our corporate name card. We are an events and Exhibition stand builder company. We would like our corporate name card to resonate what we do. I need someone to create something unique that relates to the industry that I am in. The graphic designer should be creative to incorporate the elements of my industry and try to blend in well in the design of the card. Our aim is to ensure that we are unique and our card can look different from our competitors.
Updates

Target Market(s)

Marketing and events manager from all companies

Contact Information for Business Card

The business card should have the following details:
Name
Job Title
Email
Website

Colors

Designer to choose colors to be used in the design.

Requirements
Must have
• The card must be look something that is relevant to the service that I am providing. My website is: www.velmora-buildworks.com
• You can see my website to get more information on what service that I am doing
Nice to have
• On the back of my card, I would like to have a globe image with the incorporation of my company logo. This is to indicate that my services can be done in any part of the world.

```html
<!DOCTYPE html>
<html lang="en">
<head>
<meta charset="utf-8">
<title>Velmora Buildworks – Business Card</title>
<link rel="stylesheet" href="https://fonts.googleapis.com/css2?family=Open+Sans:wght@400;600;700&display=swap">
<style>
  :root {
    --backdrop: #1c1c1e;
    --card-green: #0b7a3b;
    --map-tint: rgba(255, 255, 255, 0.12);
    --silver: #d7dadc;
    --paper: #ffffff;
    --accent-red: #e0141e;
    --ink-grey: #555a5e;
    --brand-grey: #6e7275;
    --rule-grey: #8a8d90;
    --white: #ffffff;
  }
  * { box-sizing: border-box; margin: 0; padding: 0; }
  html, body {
    width: 1200px;
    height: 960px;
    overflow: hidden;
    background: var(--backdrop);
    font-family: "Open Sans", Arial, sans-serif;
  }
  .canvas {
    position: relative;
    width: 1200px;
    height: 960px;
  }
  .card {
    position: absolute;
    left: 250px;
    width: 700px;
    height: 400px;
    overflow: hidden;
  }

  /* Back face */
  .card-back {
    top: 60px;
    background: var(--card-green);
  }
  .card-back .world-map {
    position: absolute;
    left: 40px;
    top: 30px;
    width: 620px;
    height: 300px;
    border-radius: 46% 54% 40% 60% / 50% 45% 55% 50%;
    background: radial-gradient(ellipse at 50% 45%, var(--map-tint), rgba(255,255,255,0.04) 70%, transparent 100%);
  }
  .card-back .brand-name {
    position: absolute;
    left: 0;
    right: 0;
    top: 160px;
    text-align: center;
    font-weight: 700;
    font-size: 30px;
    letter-spacing: 3px;
    color: var(--silver);
  }
  .card-back .brand-mark {
    position: absolute;
    left: 331px;
    top: 104px;
    width: 38px;
    height: 38px;
    border-radius: 50%;
    background: var(--silver);
  }
  .card-back .website {
    position: absolute;
    left: 0;
    right: 0;
    top: 240px;
    text-align: center;
    font-size: 19px;
    letter-spacing: 3px;
    color: var(--white);
  }

  /* Front face */
  .card-front {
    top: 500px;
    background: var(--paper);
  }
  .card-front .brand-mark {
    position: absolute;
    left: 478px;
    top: 40px;
    width: 40px;
    height: 40px;
    border-radius: 50%;
    background: var(--accent-red);
  }
  .card-front .brand-name {
    position: absolute;
    right: 36px;
    top: 96px;
    font-weight: 700;
    font-size: 24px;
    letter-spacing: 2px;
    color: var(--brand-grey);
  }
  .holder {
    position: absolute;
    left: 40px;
    top: 128px;
  }
  .holder-name {
    font-weight: 700;
    font-size: 22px;
    color: var(--accent-red);
    letter-spacing: 0.5px;
  }
  .holder-title {
    font-size: 15px;
    color: var(--ink-grey);
    margin-top: 2px;
  }
  .holder-rule {
    width: 100px;
    height: 4px;
    background: var(--accent-red);
    margin-top: 4px;
  }
  .contacts {
    position: absolute;
    left: 40px;
    top: 222px;
    list-style: none;
    font-size: 15px;
    color: var(--ink-grey);
    line-height: 24px;
  }
  .contacts .label {
    display: inline-block;
    width: 28px;
    font-weight: 700;
    color: var(--accent-red);
  }
  .divider {
    position: absolute;
    left: 0;
    right: 0;
    top: 300px;
    height: 1px;
    background: var(--rule-grey);
  }
  .address {
    position: absolute;
    right: 36px;
    top: 316px;
    text-align: right;
    font-size: 15px;
    line-height: 22px;
    color: var(--ink-grey);
    font-style: normal;
  }
</style>
</head>
<body>
<main class="canvas">
  <section class="card card-back" aria-label="Card back">
    <div class="world-map" role="img" aria-label="Faint world map spread across the card"></div>
    <span class="brand-mark" aria-hidden="true"></span>
    <p class="brand-name">VELMORA BUILDWORKS</p>
    <p class="website">www.velmora-buildworks.com</p>
  </section>

  <section class="card card-front" aria-label="Card front">
    <span class="brand-mark" aria-hidden="true"></span>
    <p class="brand-name">VELMORA BUILDWORKS</p>

    <div class="holder">
      <p class="holder-name">DANIEL OKAFOR</p>
      <p class="holder-title">PRESIDENT</p>
      <div class="holder-rule"></div>
    </div>

    <ul class="contacts">
      <li><span class="label">P :</span>014-552-7310</li>
      <li><span class="label">E :</span>info@velmora-buildworks.com</li>
      <li><span class="label">W :</span>www.velmora-buildworks.com</li>
    </ul>

    <div class="divider"></div>

    <address class="address">
      Street Name, City Name<br>
      Zipcode - 01234
    </address>
  </section>
</main>
</body>
</html>
```